Web design for a honey company

We are a honey retailing company currently looking for creative design for 3 pages of our existing e-commerce website which can be found here www.alpha.tolvenmarsk.co.nz. The designs need to be responsive i.e. presented in both desktop and mobile versions. We want to use the existing page color pallet, however any fonts can be used. Please use the texts and graphic content in the attachment files provided. For more detailed instructions please. The page does not require coding, the output files should be provided as layered and editable PSD.<br/><br/>Task 2: design 2 home page banners. Images, texts and the concept provided in the "layout structure" file. <br/><br/>The web designs should be presented in both desktop and mobile versions. We are looking for professional designer submissions only!

Target Market(s)

Hi-end consumers
Health conscious consumers

Number of Pages Required

3 page

Requirements
Must have
• 50% of images supplied along + any suggested stock images.
• Supplied texts integrated in the designs.
• Please only use the product images we have provided!
Should not have
• Clipart vector bees, vector honey slots or combs.
• No images of honey in glass jars!
• Do not use images of the traditional honey wooden spoons!
• Do not use images of any other but Manuka flower!

```html
<!DOCTYPE html>
<html lang="en">
<head>
<meta charset="utf-8">
<title>Tolvenmarsk Honey – Home</title>
<link href="https://fonts.googleapis.com/css2?family=Libre+Baskerville&family=Lato:wght@400;700&display=swap" rel="stylesheet">
<style>
:root{
  --navy:#0b1020;
  --ink:#1b1b1b;
  --gold:#d9b25a;
  --honey:#fcd66d;
  --cream:#fff7e2;
  --article-bg:#2b2611;
  --white:#ffffff;
  --muted:#3a3a3a;
}
*{box-sizing:border-box;margin:0;padding:0}
html,body{width:1200px;height:3560px;overflow:hidden;background:var(--white)}
body{position:relative;font-family:"Lato",sans-serif;color:var(--ink)}
.serif{font-family:"Libre Baskerville",serif}
.abs{position:absolute}

/* header */
.site-header{position:absolute;left:0;top:0;width:1200px;height:65px;background:var(--navy);z-index:3}
.menu-icon{position:absolute;left:106px;top:24px;width:22px;height:16px}
.brand-plate{position:absolute;left:515px;top:0;width:170px;height:100px;background:var(--navy);border-radius:0 0 85px 85px;display:flex;align-items:center;justify-content:center}
.brand-name{font-family:"Libre Baskerville",serif;color:var(--gold);font-size:17px;letter-spacing:1px}
.header-tools{position:absolute;right:104px;top:20px;display:flex;align-items:center;gap:22px;color:var(--gold);font-size:12px}
.header-tools .login{display:flex;align-items:center;gap:6px}

/* hero */
.hero{position:absolute;left:0;top:65px;width:1200px;height:653px;background:linear-gradient(180deg,var(--honey) 0%,#fde4a3 55%,var(--white) 100%)}
.hero-kicker{position:absolute;left:105px;top:240px;font-family:"Libre Baskerville",serif;font-size:35px;color:var(--ink)}
.hero-title{position:absolute;left:105px;top:282px;font-family:"Libre Baskerville",serif;font-size:52px;color:var(--ink)}
.hero-visual{position:absolute;left:574px;top:122px;width:600px;height:435px;border-radius:40px;background:radial-gradient(ellipse at 40% 45%,#2a1d12 0%,#1a1510 45%,rgba(240,190,200,.75) 75%,rgba(253,228,163,0) 100%)}
.dots{position:absolute;left:572px;top:606px;display:flex;gap:12px}
.dots span{width:9px;height:9px;border-radius:50%;background:var(--ink)}
.dots span.on{background:var(--gold)}

/* buttons */
.btn{position:absolute;display:flex;align-items:center;justify-content:center;gap:18px;height:38px;border:2px solid var(--ink);border-radius:19px;font-family:"Libre Baskerville",serif;font-size:12px;color:var(--ink);text-transform:uppercase}
.btn.light{border-color:var(--white);color:var(--white)}

/* section heads */
.section-title{position:absolute;left:0;width:1200px;text-align:center;font-family:"Libre Baskerville",serif;font-size:29px;color:var(--ink)}
.section-title.light{color:var(--white)}
.divider{position:absolute;left:582px;width:36px;height:20px}

/* products */
.product{position:absolute;top:940px;width:340px;text-align:center}
.product-shot{margin:0 auto;width:190px;height:235px;background:radial-gradient(ellipse at 55% 55%,#161616 0%,#2a3a2e 55%,rgba(255,255,255,0) 75%);border-radius:20px}
.product-name{margin-top:62px;font-family:"Libre Baskerville",serif;font-size:17px}
.product-price{margin-top:12px;font-size:13px;color:var(--muted)}

/* articles */
.articles{position:absolute;left:0;top:1459px;width:1200px;height:1339px;background:radial-gradient(ellipse at 30% 60%,#4a3f14 0%,var(--article-bg) 55%,#14140c 100%)}
.article{position:absolute;width:470px;color:var(--white)}
.article-media{width:470px;height:281px}
.article-title{margin-top:34px;margin-left:2px;font-family:"Libre Baskerville",serif;font-size:20px}
.article-text{margin-top:18px;margin-left:2px;font-size:11px;line-height:22.5px;width:466px}

/* newsletter */
.email-field{position:absolute;left:348px;top:3038px;width:346px;height:38px;border:2px solid var(--ink);border-radius:19px;display:flex;align-items:center;gap:10px;padding-left:20px;font-size:11px;color:var(--ink)}

/* footer */
.site-footer{position:absolute;left:0;top:3110px;width:1200px;height:400px;background:linear-gradient(180deg,var(--white) 0%,#fbefc8 45%,#f3d98a 100%)}
.footer-brand{position:absolute;left:105px;top:3222px;font-family:"Libre Baskerville",serif;font-size:22px;color:var(--ink);display:flex;align-items:center;gap:10px}
.footer-brand i{display:block;width:14px;height:14px;border-radius:50%;background:var(--gold)}
.footer-about{position:absolute;left:105px;top:3318px;width:240px;font-size:11px;line-height:22.5px;color:var(--ink)}
.pay-badges{position:absolute;left:105px;top:3425px;display:flex;gap:10px}
.pay-badges span{width:40px;height:25px;border-radius:3px;background:var(--white);border:1px solid #c9c9c9}
.footer-col{position:absolute;top:3230px}
.footer-col h4{font-family:"Libre Baskerville",serif;font-weight:400;font-size:17px;color:var(--ink);margin-bottom:56px}
.footer-col ul{list-style:none;font-size:11px;line-height:22.5px;color:var(--ink)}
.footer-col li{display:flex;gap:8px;align-items:flex-start}
.copy-bar{position:absolute;left:0;top:3510px;width:1200px;height:50px;background:var(--navy);color:var(--white)}
.copy-bar p{position:absolute;left:105px;top:18px;font-size:11px}
.socials{position:absolute;right:105px;top:12px;display:flex;gap:9px}
.socials span{width:25px;height:25px;border:1.5px solid var(--white);border-radius:50%}
</style>
</head>
<body>

<header class="site-header">
  <svg class="menu-icon" viewBox="0 0 22 16"><path d="M0 1h22M0 8h22M0 15h22" stroke="#ffffff" stroke-width="1.6"/></svg>
  <div class="brand-plate"><span class="brand-name">TOLVENMARSK</span></div>
  <div class="header-tools">
    <span class="login">
      <svg width="16" height="16" viewBox="0 0 16 16" fill="none" stroke="#ffffff" stroke-width="1.3"><circle cx="8" cy="5" r="3.5"/><path d="M1.5 15c0-3.5 3-5.5 6.5-5.5s6.5 2 6.5 5.5z"/></svg>
      Login
    </span>
    <svg width="20" height="18" viewBox="0 0 20 18" fill="none" stroke="#ffffff" stroke-width="1.4"><path d="M10 16.5S1.5 11 1.5 5.5A4 4 0 0 1 10 3.8 4 4 0 0 1 18.5 5.5C18.5 11 10 16.5 10 16.5z"/></svg>
    <svg width="22" height="20" viewBox="0 0 22 20" fill="none" stroke="#ffffff" stroke-width="1.4"><path d="M1 1.5h3.5l2.5 11.5h11l2.5-8H6"/><circle cx="8.5" cy="17" r="1.5"/><circle cx="16.5" cy="17" r="1.5"/></svg>
  </div>
</header>

<section class="hero">
  <h1 class="hero-kicker">THE PUREST TASTE OF</h1>
  <p class="hero-title">NEW ZEALAND</p>
  <a class="btn" style="left:108px;top:370px;width:142px">
    <svg width="22" height="12" viewBox="0 0 22 12" fill="none" stroke="#1b1b1b" stroke-width="1.5"><path d="M0 6h20M15 1l5 5-5 5"/></svg>Buy now
  </a>
  <div class="hero-visual" role="img" aria-label="Three jars of manuka honey with manuka flowers and a kingfisher label"></div>
  <div class="dots" style="top:606px"><span class="on"></span><span></span><span></span></div>
</section>

<h2 class="section-title" style="top:808px">FEATURED PRODUCTS</h2>
<svg class="divider" style="top:861px" viewBox="0 0 36 20"><path d="M2 10h12M22 10h12" stroke="#d9b25a" stroke-width="1.2"/><circle cx="18" cy="10" r="3" fill="#d9b25a"/></svg>

<div class="product" style="left:83px">
  <div class="product-shot" role="img" aria-label="Jar of MGO 400+ manuka honey"></div>
  <p class="product-name">MGO 400+ MANUKA HONEY</p>
  <p class="product-price">USD $25.00 – USD $35.00</p>
</div>
<div class="product" style="left:424px">
  <div class="product-shot" role="img" aria-label="Jar of MGO 800+ manuka honey"></div>
  <p class="product-name">MGO 800+ MANUKA HONEY</p>
  <p class="product-price">USD $25.00 – USD $129.00</p>
</div>
<div class="product" style="left:774px">
  <div class="product-shot" role="img" aria-label="Jar of MGO 500+ manuka honey"></div>
  <p class="product-name">MGO 500+ MANUKA HONEY</p>
  <p class="product-price">USD $25.00 – USD $35.00</p>
</div>
<a class="btn" style="left:183px;top:1306px;width:142px"><svg width="22" height="12" viewBox="0 0 22 12" fill="none" stroke="#1b1b1b" stroke-width="1.5"><path d="M0 6h20M15 1l5 5-5 5"/></svg>Buy now</a>
<a class="btn" style="left:528px;top:1306px;width:142px"><svg width="22" height="12" viewBox="0 0 22 12" fill="none" stroke="#1b1b1b" stroke-width="1.5"><path d="M0 6h20M15 1l5 5-5 5"/></svg>Buy now</a>
<a class="btn" style="left:874px;top:1306px;width:142px"><svg width="22" height="12" viewBox="0 0 22 12" fill="none" stroke="#1b1b1b" stroke-width="1.5"><path d="M0 6h20M15 1l5 5-5 5"/></svg>Buy now</a>

<section class="articles" role="img" aria-label="Blurred close-up of a yellow flower behind the articles">
  <h2 class="section-title light" style="top:74px">LATEST ARTICLES</h2>
  <svg class="divider" style="top:127px" viewBox="0 0 36 20"><path d="M2 10h12M22 10h12" stroke="#d9b25a" stroke-width="1.2"/><circle cx="18" cy="10" r="3" fill="#d9b25a"/></svg>

  <article class="article" style="left:105px;top:195px">
    <div class="article-media" role="img" aria-label="Beekeeper holding a honeycomb frame covered in bees" style="background:linear-gradient(135deg,#d9a53a,#6b4a22 55%,#3a2a18)"></div>
    <h3 class="article-title">ARTICLE TITLE # 01</h3>
    <p class="article-text">Lorem Ipsum is simply dummy text of the printing and typesetting industry. Lorem Ipsum has been the industry's standard dummy text ever since the 1500s, when an unknown printer took a galley of type and scrambled it to make a type specimen book.</p>
  </article>
  <article class="article" style="left:622px;top:195px">
    <div class="article-media" role="img" aria-label="Bee gathering pollen on a white and yellow flower" style="background:radial-gradient(ellipse at 60% 55%,#f2e200 0%,#e9e2b0 45%,#f7f5ee 80%)"></div>
    <h3 class="article-title">ARTICLE TITLE # 02</h3>
    <p class="article-text">Lorem Ipsum is simply dummy text of the printing and typesetting industry. Lorem Ipsum has been the industry's standard dummy text ever since the 1500s, when an unknown printer took a galley of type and scrambled it to make a type specimen book.</p>
  </article>
  <article class="article" style="left:105px;top:756px">
    <div class="article-media" role="img" aria-label="Video of a beekeeper in a protective suit tending hives" style="position:relative;background:linear-gradient(160deg,#4a5a6a,#6e7a5c 50%,#c9ccd0)">
      <svg style="position:absolute;left:190px;top:110px" width="86" height="60" viewBox="0 0 86 60"><rect width="86" height="60" rx="12" fill="#1b1b1b" opacity=".75"/><path d="M35 18l20 12-20 12z" fill="#ffffff"/></svg>
    </div>
    <h3 class="article-title">ARTICLE TITLE # 03</h3>
    <p class="article-text">Lorem Ipsum is simply dummy text of the printing and typesetting industry. Lorem Ipsum has been the industry's standard dummy text ever since the 1500s, when an unknown printer took a galley of type and scrambled it to make a type specimen book.</p>
  </article>
  <article class="article" style="left:622px;top:756px">
    <div class="article-media" role="img" aria-label="Bumblebee visiting white blossom" style="background:radial-gradient(ellipse at 35% 40%,#c0552a 0%,#6c6c5c 35%,#8a9a7a 70%,#c9d2c0)"></div>
    <h3 class="article-title" style="color:#5a4a1a">ARTICLE TITLE # 04</h3>
    <p class="article-text">Lorem Ipsum is simply dummy text of the printing and typesetting industry. Lorem Ipsum has been the industry's standard dummy text ever since the 1500s, when an unknown printer took a galley of type and scrambled it to make a type specimen book.</p>
  </article>

  <a class="btn light" style="left:107px;top:650px;width:156px"><svg width="22" height="12" viewBox="0 0 22 12" fill="none" stroke="#ffffff" stroke-width="1.5"><path d="M0 6h20M15 1l5 5-5 5"/></svg>Read more</a>
  <a class="btn light" style="left:627px;top:650px;width:156px"><svg width="22" height="12" viewBox="0 0 22 12" fill="none" stroke="#ffffff" stroke-width="1.5"><path d="M0 6h20M15 1l5 5-5 5"/></svg>Read more</a>
  <a class="btn light" style="left:107px;top:1211px;width:156px"><svg width="22" height="12" viewBox="0 0 22 12" fill="none" stroke="#ffffff" stroke-width="1.5"><path d="M0 6h20M15 1l5 5-5 5"/></svg>Read more</a>
  <a class="btn light" style="left:627px;top:1211px;width:156px"><svg width="22" height="12" viewBox="0 0 22 12" fill="none" stroke="#ffffff" stroke-width="1.5"><path d="M0 6h20M15 1l5 5-5 5"/></svg>Read more</a>
</section>

<h2 class="section-title" style="top:2918px">SIGNUP FOR OUR NEWSLETTER</h2>
<svg class="divider" style="top:2971px" viewBox="0 0 36 20"><path d="M2 10h12M22 10h12" stroke="#d9b25a" stroke-width="1.2"/><circle cx="18" cy="10" r="3" fill="#d9b25a"/></svg>
<div class="email-field">
  <svg width="13" height="10" viewBox="0 0 13 10"><rect width="13" height="10" rx="1" fill="#1b1b1b"/><path d="M1 1l5.5 4.5L12 1" stroke="#ffffff" fill="none"/></svg>
  Email Address
</div>
<a class="btn" style="left:704px;top:3038px;width:142px"><svg width="22" height="12" viewBox="0 0 22 12" fill="none" stroke="#1b1b1b" stroke-width="1.5"><path d="M0 6h20M15 1l5 5-5 5"/></svg>Signup</a>

<footer class="site-footer" role="img" aria-label="Soft blurred honey-toned flower background"></footer>
<div class="footer-brand"><i></i>Tolvenmarsk</div>
<p class="footer-about">Lorem Ipsum is simply dummy text of the printing and typesetting industry. Lorem Ipsum has been the industry's standard dummy text ever since the 1500s.</p>
<div class="pay-badges"><span></span><span></span><span></span></div>

<div class="footer-col" style="left:416px">
  <h4>QUICK LINKS</h4>
  <ul><li>Home</li><li>Shop</li><li>Quality</li><li>About Tolvenmarsk</li><li>Articles</li><li>Contact Us</li></ul>
</div>
<div class="footer-col" style="left:596px">
  <h4>ACCOUNTS</h4>
  <ul><li>Login</li><li>Signup</li><li>My Profile</li><li>My cart</li><li>Whishlist</li><li>Checkout</li></ul>
</div>
<div class="footer-col" style="left:752px">
  <h4>CONTACT US</h4>
  <ul>
    <li><svg width="11" height="11" viewBox="0 0 12 12" style="margin-top:6px"><path d="M2 1l2.5 0 1 3-1.5 1a7 7 0 0 0 3 3l1-1.5 3 1V10a1 1 0 0 1-1 1A9.5 9.5 0 0 1 1 2a1 1 0 0 1 1-1z" fill="#1b1b1b"/></svg>+(64) 210 000 000</li>
    <li><svg width="11" height="9" viewBox="0 0 13 10" style="margin-top:7px"><rect width="13" height="10" rx="1" fill="#1b1b1b"/><path d="M1 1l5.5 4.5L12 1" stroke="#ffffff" fill="none"/></svg>sales@tolvenmarsk.co.nz</li>
    <li><svg width="11" height="13" viewBox="0 0 11 14" style="margin-top:5px"><path d="M5.5 0A5 5 0 0 1 10.5 5c0 4-5 9-5 9s-5-5-5-9a5 5 0 0 1 5-5z" fill="#1b1b1b"/><circle cx="5.5" cy="5" r="1.8" fill="#ffffff"/></svg>Postal adress: 12 Harbour Lane,<br>Seaview 3100, New Zealand</li>
  </ul>
</div>
<div class="footer-col" style="left:985px">
  <h4>LINKS</h4>
  <ul><li>Terms &amp; Conditions</li><li>Privacy Policy</li><li>FAQs</li><li>Partnership enquiries</li></ul>
</div>

<div class="copy-bar">
  <p>Copyright © 2020 Tolvenmarsk Health Limited. All Right Reserved.</p>
  <div class="socials"><span></span><span></span><span></span><span></span><span></span></div>
</div>

</body>
</html>
```